Brightwave Reach - Business Card

We need a business card for a Social Media Marketing company that specializes in online marketing for small businesses in Canada using common Social Media platforms such as Pixlora, Chatterly, Blinkpost & Quibber.

I have uploaded a copy of our logo which I would like utilized in the business card. We would like the business card to be modern yet classy design.

Our website is www.brightwavereach.ca

Industry/Entity Type

Marketing

Contact Information for Business Card

Email: info@brightwavereach.ca
Website: www.brightwavereach.ca
Telephone: 604-555-0193

Colors

Designer to choose colors to be used in the design.

Requirements
Must have
• Social Media icons on reverse
• Please add some designs with color.

```html
<!DOCTYPE html>
<html lang="en">
<head>
<meta charset="utf-8">
<title>Brightwave Reach – Business Card</title>
<link rel="stylesheet" href="https://fonts.googleapis.com/css2?family=Roboto:wght@400;500&family=Roboto+Condensed:wght@400;700&display=swap">
<style>
  :root {
    --backdrop: #e4e4e4;
    --card-light: #f6f6f6;
    --card-dark: #3b3e41;
    --ink: #3a3d41;
    --ink-soft: #4a4d51;
    --muted: #a9a9a9;
    --rule-light: #b9b9b9;
    --paper-white: #ffffff;
    --rule-dark: #8a8c8f;
  }
  * { margin: 0; padding: 0; box-sizing: border-box; }
  html, body {
    width: 1200px; height: 960px; overflow: hidden;
    background: var(--backdrop);
  }
  .canvas { position: relative; width: 1200px; height: 960px; }

  .card { position: absolute; width: 600px; height: 343px; }
  .card--front { left: 314px; top: 113px; background: var(--card-light); }
  .card--back { left: 311px; top: 472px; background: var(--card-dark); }

  .brand-name {
    position: absolute; left: 0; width: 100%;
    text-align: center;
    font-family: "Roboto Condensed", sans-serif;
    font-weight: 700;
    font-size: 31px; line-height: 31px;
    letter-spacing: 0.5px;
    text-transform: uppercase;
  }
  .card--front .brand-name { top: 88px; color: var(--ink); }
  .card--back .brand-name { top: 118px; color: var(--paper-white); }

  .person {
    position: absolute; right: 322px; top: 230px;
    text-align: right;
    font-family: "Roboto Condensed", sans-serif;
  }
  .person__name { font-size: 20px; font-weight: 400; color: var(--ink); line-height: 26px; }
  .person__role { font-size: 14.5px; color: var(--muted); line-height: 22px; }

  .divider {
    position: absolute; left: 299px; top: 224px;
    width: 1px; height: 62px; background: var(--rule-light);
  }

  .contact {
    position: absolute; left: 320px; top: 226px;
    list-style: none;
    font-family: "Roboto", sans-serif;
    font-size: 14px; color: var(--ink-soft);
  }
  .contact li { display: flex; align-items: center; height: 19px; }
  .contact svg { width: 13px; height: 13px; margin-right: 9px; fill: var(--ink); }

  .social-row {
    position: absolute; left: 0; top: 288px; width: 100%;
    display: flex; align-items: center; justify-content: center;
    gap: 14px;
  }
  .social-row__rule { width: 90px; height: 1px; background: var(--rule-dark); }
  .social-row__names {
    display: flex; gap: 14px;
    font-family: "Roboto", sans-serif; font-size: 13px; color: var(--paper-white);
    list-style: none;
  }
  .social-row__names li { display: flex; align-items: center; gap: 5px; }
  .social-row__names li::before {
    content: ""; width: 8px; height: 8px; border-radius: 50%;
    border: 1px solid var(--paper-white);
  }
</style>
</head>
<body>
<main class="canvas">
  <section class="card card--front" aria-label="Card front">
    <h1 class="brand-name">Brightwave<br>Reach</h1>

    <div class="person">
      <p class="person__name">DANIEL REEVE</p>
      <p class="person__role">CEO/FOUNDER</p>
    </div>
    <div class="divider"></div>

    <ul class="contact">
      <li>
        <svg viewBox="0 0 24 24" aria-hidden="true"><path d="M6.6 10.8a15.1 15.1 0 0 0 6.6 6.6l2.2-2.2a1 1 0 0 1 1-.25 11.4 11.4 0 0 0 3.6.57 1 1 0 0 1 1 1V20a1 1 0 0 1-1 1A17 17 0 0 1 3 4a1 1 0 0 1 1-1h3.5a1 1 0 0 1 1 1c0 1.25.2 2.45.57 3.57a1 1 0 0 1-.25 1z"/></svg>
        604-555-0193
      </li>
      <li>
        <svg viewBox="0 0 24 24" aria-hidden="true"><path d="M2 5h20v14H2z M2 5l10 8 10-8" fill="none" stroke="currentColor"/><path d="M2 5h20l-10 7.5z M2 7l10 7.5L22 7v12H2z"/></svg>
        info@brightwavereach.ca
      </li>
      <li>
        <svg viewBox="0 0 24 24" aria-hidden="true"><circle cx="12" cy="12" r="10"/></svg>
        www.brightwavereach.ca
      </li>
    </ul>
  </section>

  <section class="card card--back" aria-label="Card back">
    <p class="brand-name">Brightwave<br>Reach</p>

    <div class="social-row">
      <span class="social-row__rule"></span>
      <ul class="social-row__names">
        <li>Chatterly</li>
        <li>Pixlora</li>
        <li>Quibber</li>
      </ul>
      <span class="social-row__rule"></span>
    </div>
  </section>
</main>
</body>
</html>
```